IT Company requires new Business Card design.

Over the years we have had a few different business card designs. We are now due for new cards across the board for all staff. We felt this would be a good time to start fresh with a new design. Our traditional card simply had our details on the front, and a list of services on the back. We don't particularly need the list of services, we have had cards where the only thing on the rear of the card was our logo.
Feel free to be creative, we would like our tag line "Complete IT Management" to appear at some point, doesn't necessarily have to be with the logo.
I have attached samples and drafts of various previous cards we have used over the years.

```html
<!DOCTYPE html>
<html lang="en">
<head>
<meta charset="utf-8">
<title>Harbour Systems – Business Card</title>
<link href="https://fonts.googleapis.com/css2?family=Open+Sans:wght@400;600;700&display=swap" rel="stylesheet">
<style>
  :root {
    --backdrop: #e6e3df;
    --card: #ffffff;
    --brand: #5f6d78;
    --ink: #3a3f44;
    --rule: #8a949c;
  }
  * { margin: 0; padding: 0; box-sizing: border-box; }
  html, body {
    width: 1034px; height: 1200px; overflow: hidden;
    background: var(--backdrop);
    font-family: "Open Sans", Arial, sans-serif;
    color: var(--ink);
  }
  .canvas { position: relative; width: 1034px; height: 1200px; }
  .card {
    position: absolute; left: 74px; width: 900px; height: 511px;
    background: var(--card); border-radius: 38px;
    box-shadow: 0 2px 6px rgba(0,0,0,0.12);
  }
  .card--front { top: 65px; }
  .card--back { top: 631px; }

  .brand-lockup { position: absolute; left: 46px; top: 200px; width: 400px; }
  .brand-name {
    display: flex; align-items: center; gap: 16px;
    font-weight: 700; font-size: 40px; line-height: 1; color: var(--brand);
    letter-spacing: 0.5px; text-transform: uppercase;
  }
  .brand-mark { width: 44px; height: 44px; background: var(--brand); flex: none; }
  .tagline {
    margin: 14px 0 0 60px; font-size: 14px; font-weight: 600;
    letter-spacing: 3.4px; text-transform: uppercase; color: var(--brand);
  }

  .details {
    position: absolute; left: 468px; top: 82px; height: 350px;
    border-left: 2px solid var(--rule); padding-left: 24px;
  }
  .details::before {
    content: ""; position: absolute; left: -4px; top: 0;
    width: 6px; height: 38px; background: var(--brand);
  }
  .person-name { font-weight: 700; font-size: 29px; line-height: 38px; color: var(--brand); }
  .person-role { font-size: 22px; line-height: 32px; color: var(--ink); }
  .contact-list { list-style: none; margin-top: 22px; }
  .contact-list li {
    display: flex; align-items: center; gap: 10px;
    font-size: 21px; line-height: 34px; color: var(--ink);
  }
  .contact-list svg { width: 18px; height: 18px; fill: var(--ink); flex: none; }
  .address { margin-top: 22px; font-size: 21px; line-height: 31px; color: var(--ink); }

  .back-brand {
    position: absolute; left: 0; right: 0; top: 95px;
    display: flex; flex-direction: column; align-items: center; gap: 34px;
  }
  .back-brand .brand-mark { width: 150px; height: 150px; }
  .back-brand .brand-name { font-size: 58px; }
  .back-url {
    position: absolute; left: 0; right: 0; top: 462px; text-align: center;
    font-size: 25px; letter-spacing: 2.6px; color: var(--ink);
  }
</style>
</head>
<body>
<div class="canvas">
  <section class="card card--front">
    <div class="brand-lockup">
      <div class="brand-name"><span class="brand-mark"></span>Harbour Systems</div>
      <div class="tagline">Complete IT Management</div>
    </div>

    <div class="details">
      <div class="person-name">Daniel Reeve</div>
      <div class="person-role">Operation Manager</div>
      <ul class="contact-list">
        <li><svg viewBox="0 0 24 24" aria-hidden="true"><path d="M6.6 10.8a15 15 0 0 0 6.6 6.6l2.2-2.2a1 1 0 0 1 1-.25 11.4 11.4 0 0 0 3.6.57 1 1 0 0 1 1 1V20a1 1 0 0 1-1 1A17 17 0 0 1 3 4a1 1 0 0 1 1-1h3.5a1 1 0 0 1 1 1c0 1.25.2 2.45.57 3.6a1 1 0 0 1-.25 1z"/></svg>08 5550 1841</li>
        <li><svg viewBox="0 0 24 24" aria-hidden="true"><path d="M8 1h8a2 2 0 0 1 2 2v18a2 2 0 0 1-2 2H8a2 2 0 0 1-2-2V3a2 2 0 0 1 2-2zm0 3v12h8V4zm4 14a1.3 1.3 0 1 0 0 2.6A1.3 1.3 0 0 0 12 18z"/></svg>0400 555 718</li>
        <li><svg viewBox="0 0 24 24" aria-hidden="true"><path d="M7 2h8l3 3v5H7zm-3 9h16a2 2 0 0 1 2 2v7a1 1 0 0 1-1 1H3a1 1 0 0 1-1-1v-7a2 2 0 0 1 2-2zm2 4v2h4v-2z"/></svg>08 5550 1841</li>
        <li><svg viewBox="0 0 24 24" aria-hidden="true"><path d="M2 5h20v14H2zm2 2v.5l8 5.5 8-5.5V7zm0 3v7h16v-7l-8 5.5z"/></svg>daniel@harboursystems.com.au</li>
        <li><svg viewBox="0 0 24 24" aria-hidden="true"><path d="M12 2a10 10 0 1 0 0 20 10 10 0 0 0 0-20zm6.9 6h-2.9a15 15 0 0 0-1.4-3.6A8 8 0 0 1 18.9 8zM12 4c.8 1.1 1.5 2.5 1.9 4h-3.8c.4-1.5 1.1-2.9 1.9-4zM4.3 14a8 8 0 0 1 0-4h3.4a16 16 0 0 0 0 4zm.8 2h2.9a15 15 0 0 0 1.4 3.6A8 8 0 0 1 5.1 16zM8 8H5.1a8 8 0 0 1 4.3-3.6A15 15 0 0 0 8 8zm4 12c-.8-1.1-1.5-2.5-1.9-4h3.8c-.4 1.5-1.1 2.9-1.9 4zm2.3-6H9.7a14 14 0 0 1 0-4h4.6a14 14 0 0 1 0 4zm.3 5.6A15 15 0 0 0 16 16h2.9a8 8 0 0 1-4.3 3.6zM16.3 14a16 16 0 0 0 0-4h3.4a8 8 0 0 1 0 4z"/></svg>www.harboursystems.com.au</li>
      </ul>
      <div class="address">Unit 7 22 Marlow Court<br>Brookvale WA 6190</div>
    </div>
  </section>

  <section class="card card--back">
    <div class="back-brand">
      <span class="brand-mark"></span>
      <div class="brand-name">Harbour Systems</div>
    </div>
    <div class="back-url">www.harboursystems.com.au</div>
  </section>
</div>
</body>
</html>
```